International Petrochemical business needs a web design for Clearway Desk system

We need a web design for a "Clearway Desk" system for an international petrochemical company. The web site is used internally within the company. It is hosted by an internal department which provides government permit request service for other departments.

We would like to see designs of two pages using color light blue. (home page, internal page as attached).
Home Page:
1. Header has a background image and small animation. Header on home page can be taller than the header of the internal page.
2. Layout as attached.

Internal Page:
1. Header can use the same background image as the home page and can be shorter to utilize the page for content.
2. The blue icon behind every captions represent an icon. When user move mouse over this icon, it displays the caption in Thai language as a tooltip. This icon needs to be redesign.

The final design should communicate the followings:
- Excellent service provided system in terms of time and accurary
- Rapid growth of business via building petrochemical refinery plant
Updates

For Internal Page, the blue circle behind every captions represent an icon. When mouse over this icon, a tool tip showing the caption in Thai language is shown. Please also design this icon..

There are more feedbacks from customer as followed:

1. Banner should consists of 
    1.1 "Approved" stamp on paper
    1.2 An image of Garuda. It is used on every government documents in Thailand
    1.3 Image of petrochemical plant
2. Each menu item (Home, Permit, Search, etc) should have different colors. Drop down menu will use the same color as its parent menu item.
3. Overall tone of the web page should be light blue with background of the body the web page in white
4. "New Request" button should use green color with icon on it
5. Table header of each box in the body of the page should use dark blue background with text in white

Please kindly submit your revisions.
Thank you.

Industry/Entity Type

Business

Requirements
Must have
• 1. Design for 1024x768 screen resolution
2. Use light blue theme
3. Background of header where the company logo is must have white background

```html
<!DOCTYPE html>
<html lang="en">
<head>
<meta charset="utf-8">
<title>Clearway Desk – Request Form</title>
<link rel="stylesheet" href="https://fonts.googleapis.com/css2?family=Roboto:wght@400;500;700;900&family=Sarabun:wght@500&display=swap">
<style>
:root{
  --navy:#0d2f66;
  --navy-dark:#0a2247;
  --panel:#cfe6fb;
  --panel-edge:#a9c9e8;
  --label:#1b1b1b;
  --field:#ffffff;
  --field-edge:#c3c9cf;
  --link:#2a6dd0;
  --nav-home:#0d2f66;
  --nav-permits:#7a0b86;
  --nav-search:#0f8c63;
  --nav-report:#c45a08;
  --nav-admin:#c10a12;
  --nav-help:#5b5b5b;
  --icon-top:#f3f8fd;
  --icon-bottom:#bfd5ea;
  --icon-ink:#1c5fa8;
  --chip:#b7bcc2;
}
*{box-sizing:border-box;margin:0;padding:0}
html,body{width:834px;height:1200px;overflow:hidden;background:#fff}
body{position:relative;font-family:"Roboto",Arial,sans-serif;color:var(--label)}
.abs{position:absolute}

.site-header{position:absolute;left:0;top:0;width:834px;height:79px;background:#fff}
.brand{position:absolute;left:60px;top:16px;display:flex;align-items:center;gap:7px}
.brand-dot{width:24px;height:24px;border-radius:50%;background:#1f8de0}
.brand-name{font-weight:700;font-size:15px;color:#1f6fc4;line-height:1}
.site-title{position:absolute;left:0;width:834px;top:28px;text-align:center;font-weight:900;font-size:28px;letter-spacing:.5px;color:var(--navy)}

.main-nav{position:absolute;top:79px;left:0;height:23px}
.main-nav a{position:absolute;top:0;height:23px;line-height:23px;text-align:center;color:#fff;font-size:11px;font-weight:500;text-decoration:none}

.banner{position:absolute;left:0;top:102px;width:834px;height:128px;
  background:linear-gradient(180deg,#e4e7ea 0%,#c9ced3 45%,#8e979f 100%)}

.form-panel{position:absolute;left:48px;top:247px;width:758px;height:862px;border-radius:10px;background:var(--panel);
  border:1px solid var(--panel-edge);box-shadow:0 6px 10px rgba(0,0,0,.18)}
.form-head{height:35px;border-radius:10px 10px 0 0;background:linear-gradient(180deg,#2b5f9e,#0f3a73 60%,#0c2f5f);
  color:#fff;font-weight:700;font-size:14px;line-height:34px;padding-left:10px}

.label{position:absolute;font-size:11.5px;font-weight:500;text-align:right;white-space:nowrap}
.label .req{color:#d0202a;font-size:9px;vertical-align:top;margin-left:2px}
.icon{position:absolute;width:28px;height:28px;border-radius:7px;border:1px solid #8fa8c2;
  background:linear-gradient(180deg,var(--icon-top),var(--icon-bottom));display:flex;align-items:center;justify-content:center}
.icon svg{width:18px;height:18px}
.colon{position:absolute;font-size:12px;font-weight:700}
.field{position:absolute;height:20px;background:var(--field);border:1px solid var(--field-edge);border-radius:3px;
  box-shadow:inset 0 3px 4px rgba(0,0,0,.08);font-size:11.5px;color:#444;line-height:18px;padding-left:8px}
.select::after{content:"";position:absolute;right:6px;top:5px;border-left:5px solid transparent;border-right:5px solid transparent;border-top:8px solid #7a7a7a}
.area{line-height:15px;padding-top:5px;box-shadow:inset 0 6px 6px rgba(0,0,0,.12)}
.btn{position:absolute;height:20px;border:1px solid #a3a9af;border-radius:4px;background:linear-gradient(180deg,#f4f4f4,#cfd2d5);
  font-size:9.5px;color:#555;text-align:center;line-height:18px;font-weight:500}
.chip{position:absolute;height:14px;border-radius:3px;background:var(--chip);font-size:7.5px;color:#555;line-height:14px;padding-left:4px;border:1px solid #a9aeb3;white-space:nowrap}
.chip b{position:absolute;right:0;top:-1px;width:18px;height:14px;background:#eceef0;border:1px solid #a9aeb3;border-radius:3px;text-align:center;font-size:8px;color:#333}

.tooltip{position:absolute;left:495px;top:363px;width:132px;height:37px;background:var(--navy);border-radius:4px;
  color:#fff;font-family:"Sarabun",sans-serif;font-size:8.5px;line-height:12px;padding:6px 9px;white-space:nowrap;overflow:hidden}
.tooltip::before{content:"";position:absolute;left:98px;top:-6px;border-left:6px solid transparent;border-right:6px solid transparent;border-bottom:6px solid var(--navy)}
.tooltip-wrap{position:absolute;left:495px;top:357px;width:132px;height:6px}

.related{position:absolute;left:229px;top:931px;width:321px;height:124px;background:#fff;border-radius:4px;border:1px solid #c7ccd1;overflow:hidden}
.related table{border-collapse:collapse;width:100%;font-size:9.5px}
.related th{height:27px;background:linear-gradient(180deg,#fbfbfb,#d8dbde);text-align:left;font-weight:500;font-size:10.5px;color:#333;padding-left:10px;border-right:1px solid #c0c4c8}
.related th:last-child{border-right:none}
.related td{height:14.5px;padding-left:10px;color:#222;border-right:1px solid #d4d8dc}
.related td:last-child{border-right:none}
.related tr:first-child+tr td{padding-top:6px;height:20px}
.related a{color:var(--link)}
.pager{position:absolute;left:343px;top:1034px;width:102px;height:21px;background:var(--navy);border-radius:10px 10px 0 0;display:flex;align-items:center;justify-content:center;gap:4px;color:#fff;font-size:8px;font-weight:700}
.pager span{width:11px;height:11px;border-radius:50%;text-align:center;line-height:11px}
.pager .arrow{font-size:12px}
.pager .on{background:#fff;color:var(--navy)}

.action{position:absolute;height:27px;border:1px solid #9aa1a8;border-radius:4px;background:linear-gradient(180deg,#f6f6f6,#c8ccd0);
  font-weight:700;font-size:12px;color:#666;line-height:25px;text-align:center}

.site-footer{position:absolute;left:0;top:1128px;width:834px;height:72px;background:linear-gradient(180deg,#0f3566,#0a2447)}
.site-footer p{position:absolute;top:14px;font-size:8px;color:#e3ecf6}
</style>
</head>
<body>

<header class="site-header">
  <div class="brand"><span class="brand-dot"></span><span class="brand-name">Norvane Petrochemical</span></div>
  <div class="site-title">CLEARWAY DESK</div>
</header>

<nav class="main-nav">
  <a href="#" style="left:172px;width:72px;background:var(--nav-home)">HOME</a>
  <a href="#" style="left:257px;width:73px;background:var(--nav-permits)">PERMITS</a>
  <a href="#" style="left:346px;width:72px;background:var(--nav-search)">SEARCH</a>
  <a href="#" style="left:430px;width:73px;background:var(--nav-report)">REPORT</a>
  <a href="#" style="left:512px;width:71px;background:var(--nav-admin)">ADMIN</a>
  <a href="#" style="left:591px;width:72px;background:var(--nav-help)">HELP</a>
</nav>

<div class="banner" role="img" aria-label="Petrochemical plant with storage spheres, a red approved stamp and the national emblem"></div>

<section class="form-panel"><div class="form-head">Request Form</div></section>

<!-- left column labels -->
<div class="label" style="right:656px;top:302px">Request Date</div>
<div class="label" style="right:656px;top:338px">Requester Name</div>
<div class="label" style="right:656px;top:374px">Contact No</div>
<div class="label" style="right:656px;top:409px">Company<span class="req">*</span></div>
<div class="label" style="right:656px;top:445px">Branch<span class="req">*</span></div>
<div class="label" style="right:656px;top:480px">Document Category<span class="req">*</span></div>
<div class="label" style="right:656px;top:516px">Document Type<span class="req">*</span></div>
<div class="label" style="right:656px;top:551px">Expected Use Date<span class="req">*</span></div>
<div class="label" style="right:656px;top:587px">Detail<span class="req">*</span></div>
<div class="label" style="right:656px;top:675px">Attachment</div>
<div class="label" style="right:656px;top:729px">Coordinator<span class="req">*</span></div>
<div class="label" style="right:656px;top:782px">Related Person<span class="req">*</span></div>
<div class="label" style="right:656px;top:852px">Remark</div>
<div class="label" style="right:656px;top:941px">Related Request</div>

<!-- icons -->
<div class="icon" style="left:183px;top:294px"><svg viewBox="0 0 18 18"><rect x="2" y="3" width="14" height="13" rx="1.5" fill="none" stroke="var(--icon-ink)" stroke-width="1.6"/><rect x="2" y="3" width="14" height="4" fill="var(--icon-ink)"/><rect x="7" y="10" width="4" height="3" fill="var(--icon-ink)"/></svg></div>
<div class="icon" style="left:183px;top:330px"><svg viewBox="0 0 18 18"><rect x="1.5" y="4" width="15" height="11" rx="1.5" fill="none" stroke="var(--icon-ink)" stroke-width="1.6"/><circle cx="6" cy="8.5" r="2" fill="var(--icon-ink)"/><rect x="9.5" y="7" width="5" height="1.5" fill="var(--icon-ink)"/><rect x="9.5" y="10" width="5" height="1.5" fill="var(--icon-ink)"/></svg></div>
<div class="icon" style="left:183px;top:366px"><svg viewBox="0 0 18 18"><rect x="5" y="1.5" width="8" height="15" rx="1.5" fill="none" stroke="var(--icon-ink)" stroke-width="1.6"/><rect x="7" y="4" width="4" height="5" fill="var(--icon-ink)"/></svg></div>
<div class="icon" style="left:183px;top:401px"><svg viewBox="0 0 18 18"><rect x="2" y="5" width="14" height="10" fill="var(--icon-ink)"/><rect x="4" y="8" width="2" height="3" fill="#fff"/><rect x="8" y="8" width="2" height="3" fill="#fff"/><rect x="12" y="8" width="2" height="3" fill="#fff"/></svg></div>
<div class="icon" style="left:183px;top:437px"><svg viewBox="0 0 18 18"><rect x="6" y="2" width="6" height="4" fill="var(--icon-ink)"/><rect x="1.5" y="12" width="5" height="4" fill="var(--icon-ink)"/><rect x="11.5" y="12" width="5" height="4" fill="var(--icon-ink)"/><path d="M9 6v3M4 12V9h10v3" fill="none" stroke="var(--icon-ink)" stroke-width="1.4"/></svg></div>
<div class="icon" style="left:183px;top:472px"><svg viewBox="0 0 18 18"><path d="M4 2h7l3 3v11H4z" fill="none" stroke="var(--icon-ink)" stroke-width="1.6"/><path d="M6 8h6M6 11h6M6 14h4" stroke="var(--icon-ink)" stroke-width="1.2"/></svg></div>
<div class="icon" style="left:183px;top:508px"><svg viewBox="0 0 18 18"><path d="M4 2h7l3 3v11H4z" fill="none" stroke="var(--icon-ink)" stroke-width="1.6"/><rect x="5.5" y="10" width="7" height="3" fill="var(--icon-ink)"/></svg></div>
<div class="icon" style="left:183px;top:543px"><svg viewBox="0 0 18 18"><rect x="2" y="3" width="14" height="13" rx="1.5" fill="none" stroke="var(--icon-ink)" stroke-width="1.6"/><rect x="2" y="3" width="14" height="3.5" fill="var(--icon-ink)"/><path d="M8 9l2-1v6" fill="none" stroke="var(--icon-ink)" stroke-width="1.6"/></svg></div>
<div class="icon" style="left:183px;top:579px"><svg viewBox="0 0 18 18"><rect x="2" y="2" width="12" height="14" fill="none" stroke="var(--icon-ink)" stroke-width="1.6"/><path d="M4.5 6h7M4.5 9h5" stroke="var(--icon-ink)" stroke-width="1.2"/><path d="M9 15l7-5" stroke="var(--icon-ink)" stroke-width="2"/></svg></div>
<div class="icon" style="left:183px;top:667px"><svg viewBox="0 0 18 18"><path d="M12 5l-6 6a2 2 0 0 0 3 3l6-6a3.5 3.5 0 0 0-5-5L4 9" fill="none" stroke="var(--icon-ink)" stroke-width="1.5"/></svg></div>
<div class="icon" style="left:183px;top:721px"><svg viewBox="0 0 18 18"><circle cx="9" cy="5.5" r="3.2" fill="var(--icon-ink)"/><path d="M3 16c0-4 2.5-6 6-6s6 2 6 6z" fill="var(--icon-ink)"/></svg></div>
<div class="icon" style="left:183px;top:774px"><svg viewBox="0 0 18 18"><circle cx="6" cy="6" r="2.6" fill="var(--icon-ink)"/><circle cx="12.5" cy="6" r="2.6" fill="var(--icon-ink)"/><path d="M1 15c0-3 2-5 5-5s5 2 5 5zM8 15c0-3 2-5 4.5-5S17 12 17 15z" fill="var(--icon-ink)"/></svg></div>
<div class="icon" style="left:183px;top:844px"><svg viewBox="0 0 18 18"><rect x="1.5" y="4" width="15" height="10" rx="2" fill="none" stroke="var(--icon-ink)" stroke-width="1.6"/><circle cx="6" cy="9" r="1.1" fill="var(--icon-ink)"/><circle cx="9" cy="9" r="1.1" fill="var(--icon-ink)"/><circle cx="12" cy="9" r="1.1" fill="var(--icon-ink)"/></svg></div>
<div class="icon" style="left:183px;top:933px"><svg viewBox="0 0 18 18"><ellipse cx="8" cy="7.5" rx="6.5" ry="4.5" fill="var(--icon-ink)"/><path d="M4 11l-1 4 4-3z" fill="var(--icon-ink)"/><ellipse cx="11.5" cy="11" rx="4.5" ry="3" fill="#6fa4d8"/></svg></div>

<!-- colons -->
<div class="colon" style="left:219px;top:302px">:</div>
<div class="colon" style="left:219px;top:338px">:</div>
<div class="colon" style="left:219px;top:374px">:</div>
<div class="colon" style="left:219px;top:409px">:</div>
<div class="colon" style="left:219px;top:445px">:</div>
<div class="colon" style="left:219px;top:480px">:</div>
<div class="colon" style="left:219px;top:516px">:</div>
<div class="colon" style="left:219px;top:551px">:</div>
<div class="colon" style="left:219px;top:587px">:</div>
<div class="colon" style="left:219px;top:675px">:</div>
<div class="colon" style="left:219px;top:729px">:</div>
<div class="colon" style="left:219px;top:782px">:</div>
<div class="colon" style="left:219px;top:852px">:</div>
<div class="colon" style="left:219px;top:941px">:</div>

<!-- fields -->
<div class="field" style="left:230px;top:298px;width:36px">21</div>
<div class="field select" style="left:273px;top:298px;width:73px">January</div>
<div class="field" style="left:353px;top:298px;width:45px">2013</div>
<div class="field" style="left:230px;top:334px;width:207px">Owen Hale</div>
<div class="field" style="left:230px;top:370px;width:207px">0890 5512 3871</div>
<div class="field select" style="left:230px;top:405px;width:207px">Please select</div>
<div class="field select" style="left:230px;top:441px;width:207px">Please select</div>
<div class="field select" style="left:230px;top:476px;width:207px">Please select</div>
<div class="field select" style="left:230px;top:512px;width:207px">Please select</div>
<div class="field" style="left:230px;top:547px;width:36px">28</div>
<div class="field select" style="left:273px;top:547px;width:73px">January</div>
<div class="field" style="left:353px;top:547px;width:45px">2013</div>
<div class="field area" style="left:230px;top:580px;width:207px;height:72px">Lorem ipsum dolor sit amet</div>
<div class="field" style="left:230px;top:671px;width:207px">confidential.doc</div>
<div class="btn" style="left:443px;top:671px;width:59px">BROWSE</div>
<div class="btn" style="left:509px;top:671px;width:59px">ATTACH</div>
<div class="chip" style="left:230px;top:696px;width:63px">file1.doc<b>X</b></div>
<div class="chip" style="left:298px;top:696px;width:63px">file1.doc<b>X</b></div>
<div class="chip" style="left:366px;top:696px;width:63px">file1.doc<b>X</b></div>
<div class="btn" style="left:231px;top:725px;width:59px">ADD</div>
<div class="chip" style="left:231px;top:749px;width:89px">Owen Hale HR<b>X</b></div>
<div class="btn" style="left:231px;top:778px;width:59px">ADD</div>
<div class="chip" style="left:231px;top:800px;width:89px">Rita Vale (IT)<b>X</b></div>
<div class="chip" style="left:325px;top:800px;width:105px">Paul Nesbit (Finance)<b>X</b></div>
<div class="chip" style="left:231px;top:817px;width:112px">Leon Marsh (Finance)<b>X</b></div>
<div class="field area" style="left:230px;top:845px;width:207px;height:70px">Lorem ipsum dolor sit amet</div>

<!-- right column -->
<div class="label" style="right:256px;top:302px">Requester Employee No</div>
<div class="label" style="right:256px;top:338px">Telephone</div>
<div class="icon" style="left:584px;top:294px;border-radius:50%"><svg viewBox="0 0 18 18"><circle cx="9" cy="9" r="7" fill="var(--icon-ink)"/><text x="9" y="12" font-size="7" font-weight="700" fill="#fff" text-anchor="middle" font-family="Roboto,sans-serif">ID</text></svg></div>
<div class="icon" style="left:584px;top:330px"><svg viewBox="0 0 18 18"><path d="M4 2.5l3 3-1.8 2a9 9 0 0 0 5.3 5.3l2-1.8 3 3-2 2.2C8 16 2 10 1.8 4.5z" fill="var(--icon-ink)"/></svg></div>
<div class="colon" style="left:620px;top:302px">:</div>
<div class="colon" style="left:620px;top:338px">:</div>
<div class="field" style="left:630px;top:298px;width:148px">3308 71264 5120</div>
<div class="field" style="left:630px;top:334px;width:148px">2731 8804 512</div>
<div class="tooltip">ระหว่างดำเนินการรอดำเนินการ<br>รอตรวจสอบ</div>

<!-- related requests -->
<div class="related">
  <table>
    <tr><th style="width:87px">Request No.</th><th style="width:86px">Request Date</th><th style="width:70px">Company</th><th>Branch</th></tr>
    <tr><td><a href="#">AB56001</a></td><td>20/4/2013</td><td>NVP</td><td>GC1</td></tr>
    <tr><td><a href="#">BIO5502</a></td><td>21/4/2013</td><td>NVP</td><td>GC2</td></tr>
    <tr><td><a href="#">AB56001</a></td><td>20/4/2013</td><td>XYZ</td><td>GC3</td></tr>
    <tr><td><a href="#">BIO5502</a></td><td>21/4/2013</td><td>XYZ</td><td>GC4</td></tr>
  </table>
</div>
<div class="pager"><span class="arrow">‹</span><span class="on">1</span><span>2</span><span>3</span><span>4</span><span>5</span><span class="arrow">›</span></div>

<div class="action" style="left:229px;top:1064px;width:90px;text-align:left;padding-left:46px">BACK
  <svg class="abs" style="left:8px;top:5px" width="22" height="16" viewBox="0 0 22 16"><rect x="0" y="0" width="22" height="16" rx="3" fill="#e6e8ea" stroke="#a3a9af"/><path d="M13 3l-5 5 5 5" fill="none" stroke="#444" stroke-width="2"/></svg>
</div>
<div class="action" style="left:327px;top:1064px;width:222px">CREATE NEW REQUEST</div>

<footer class="site-footer" role="img" aria-label="Dark blue footer over a faint plant backdrop">
  <p style="left:61px">Copyright © 2013 NorvanePetrochemical. All rights reserved.</p>
  <p style="right:39px">Terms and Condition | Privacy</p>
</footer>

</body>
</html>
```